Bramblewood Joinery Website

My client Bramblewood Joinery is looking for a redesign for a Word Press Website. Their current site is at www.bramblewoodjoinery.example They are a custom cabinet company, but also create bathroom, living room, bar and entertainment and bedroom cabinets too. They would like a design that emulates the master craftsman work they do yet a contemporary style.

Their current site was designed using Flash elements.

Target Market(s)

Home owners and builders of high end homes

Industry/Entity Type

Entertainment

Font styles to use
Serif
Decorative

Requirements
Must have
• Must show their work and logo using a contemporary style.
Nice to have
• Sliders that showcase their projects.

```html
<!DOCTYPE html>
<html lang="en">
<head>
<meta charset="utf-8">
<title>Bramblewood Joinery</title>
<link rel="stylesheet" href="https://fonts.googleapis.com/css2?family=Open+Sans:wght@400;600&family=Roboto:wght@400;500&display=swap">
<style>
:root{
  --green:#3aa83a;
  --green-dark:#2f8f2f;
  --ink:#2a2a2a;
  --text:#555;
  --muted:#777;
  --band:#ececec;
  --panel:#f3f3f3;
  --line:#e2e2e2;
  --social:#8a8a8a;
  --white:#fff;
}
*{box-sizing:border-box;margin:0;padding:0}
html,body{width:769px;height:1200px;overflow:hidden;background:var(--white);font-family:"Open Sans",Arial,sans-serif;color:var(--text)}
.page{position:relative;width:769px;height:1200px}
.abs{position:absolute}
.hero-band{left:0;top:118px;width:769px;height:347px;background:var(--band)}
.contact-top{left:63px;top:30px;display:flex;gap:9px;align-items:center}
.round-icon{width:26px;height:26px;border-radius:50%;border:1px solid var(--line);display:flex;align-items:center;justify-content:center;background:var(--white)}
.contact-top .lines{font-size:8.5px;line-height:16px;color:var(--muted)}
.contact-top .lines b{font-weight:600;color:var(--ink);font-size:9px}
.brand{left:284px;top:30px;width:200px;text-align:center}
.brand .dot{width:26px;height:26px;border-radius:50%;background:var(--green);margin:0 auto 6px}
.brand span{font-size:15px;font-weight:600;color:var(--ink)}
.search{left:596px;top:38px;width:110px;height:21px;border:1px solid var(--line);font-size:7px;color:#999;padding:6px 7px;display:flex;justify-content:space-between}
.nav{left:63px;top:99px;width:642px;height:37px;background:var(--green);border-bottom:3px solid var(--green-dark);display:flex;border-radius:2px}
.nav a{color:var(--white);text-decoration:none;font-size:10px;display:flex;align-items:center;padding:0 16.5px;border-right:1px solid rgba(0,0,0,.12)}
.nav a:last-child{border-right:none}
.slider{left:63px;top:150px;width:642px;height:314px;background:linear-gradient(180deg,#e8e4de 0%,#b9a58e 45%,#7a5a3e 100%)}
.caption{left:0;bottom:0;width:642px;height:63px;background:rgba(30,30,30,.6);padding:12px 16px}
.caption h2{font-family:Roboto,Arial,sans-serif;font-weight:400;font-size:18px;color:var(--white)}
.caption p{font-family:Roboto,Arial,sans-serif;font-size:7.5px;color:#eee;margin-top:5px}
.arrows{right:16px;top:24px;display:flex;gap:5px}
.arrows span{width:17px;height:17px;border-radius:50%;background:#1c1c1c;display:flex;align-items:center;justify-content:center}
.card{top:493px;width:151px;height:196px;background:#f6f6f6;text-align:center}
.card .photo{height:121px}
.card h3{font-weight:400;font-size:9.5px;color:var(--ink);margin:10px 0 6px;letter-spacing:.3px}
.card p{font-size:6.5px;line-height:13px;color:var(--muted);padding:0 14px}
.welcome{left:63px;top:720px;width:350px}
.welcome h1{font-weight:400;font-size:16.5px;color:var(--ink)}
.welcome p{font-size:6.6px;line-height:13px;color:#333;margin-top:8px}
.ticks{display:grid;grid-template-columns:137px 160px;row-gap:7px;font-size:8.5px;color:#333}
.ticks li{list-style:none;display:flex;align-items:center;gap:7px;line-height:12px}
.tick{width:8px;height:8px;border-radius:50%;background:var(--green);display:inline-flex;align-items:center;justify-content:center}
.welcome-list{left:63px;top:814px}
.btn{left:64px;top:882px;width:125px;height:26px;background:var(--green);color:var(--white);font-size:10px;display:flex;align-items:center;justify-content:center;border-bottom:2px solid var(--green-dark)}
.video{left:447px;top:725px;width:259px;height:184px;border:1px solid #ccc;background:#222}
.video .frame{height:164px;background:linear-gradient(160deg,#6a5f52 0%,#2b2420 55%,#4a3d31 100%)}
.video .bar{height:18px;background:#f2f2f2;display:flex;align-items:center;gap:8px;padding:0 8px;font-size:5px;color:#444}
.banner{left:63px;top:948px;width:643px;height:111px;background:var(--panel);border:1px solid var(--line)}
.banner h2{position:absolute;left:17px;top:12px;font-weight:400;font-size:13px;line-height:20px;color:var(--ink)}
.banner .ticks{position:absolute;left:19px;top:64px;grid-template-columns:160px 150px;row-gap:7px}
.truck{left:347px;top:12px;width:282px;height:88px;border-radius:4px;background:linear-gradient(90deg,#d9d2c4,#b89a6a 60%,#e6e6e6)}
.foot-band{left:0;top:1085px;width:769px;height:71px;background:var(--band)}
.foot-item{display:flex;gap:10px;align-items:center;font-size:8px;line-height:16px;color:#444}
.foot-item .round-icon{width:36px;height:36px}
.social{left:598px;top:1109px;display:flex;gap:3px}
.social span{width:24px;height:24px;border-radius:50%;background:var(--social);display:flex;align-items:center;justify-content:center}
.bottom{left:0;top:1156px;width:769px;height:44px;background:var(--green);color:var(--white);font-size:8px;display:flex;align-items:center;padding:0 63px;justify-content:space-between}
.bottom nav{display:flex;gap:5px}
</style>
</head>
<body>
<div class="page">
  <div class="abs hero-band"></div>

  <div class="abs contact-top">
    <div class="round-icon"><svg width="11" height="11" viewBox="0 0 24 24"><path fill="#888" d="M6.6 10.8a15 15 0 006.6 6.6l2.2-2.2c.3-.3.7-.4 1-.2 1.1.4 2.3.6 3.6.6.6 0 1 .4 1 1V20c0 .6-.4 1-1 1A17 17 0 013 4c0-.6.4-1 1-1h3.5c.6 0 1 .4 1 1 0 1.3.2 2.5.6 3.6.1.3 0 .7-.2 1z"/></svg></div>
    <div class="lines">info@bramblewoodjoinery.example<br><b>+1 555 014 8586</b></div>
  </div>

  <div class="abs brand"><div class="dot"></div><span>Bramblewood Joinery</span></div>

  <div class="abs search">Search<svg width="8" height="8" viewBox="0 0 10 10"><circle cx="4" cy="4" r="3" stroke="#999" fill="none"/><path d="M6.3 6.3L9 9" stroke="#999"/></svg></div>

  <nav class="abs nav">
    <a>Home</a><a>Who We Are</a><a>Getting Started</a><a>Customer Experience</a><a>Professional</a><a>Portfolio</a><a>Contact Us</a>
  </nav>

  <div class="abs slider" role="img" aria-label="Bright living room with white sofas, chandelier and wood floor">
    <div class="abs caption">
      <h2>ENTERTAINMENT AND BEDROOM CABINETS</h2>
      <p>Sed ut perspiciatis unde omnis iste natus error sit voluptatem accusantium doloremque laudantium, totam rem aperiam,</p>
      <div class="abs arrows">
        <span><svg width="6" height="8" viewBox="0 0 6 8"><path d="M5 1L2 4l3 3" stroke="#fff" stroke-width="1.4" fill="none"/></svg></span>
        <span><svg width="6" height="8" viewBox="0 0 6 8"><path d="M1 1l3 3-3 3" stroke="#fff" stroke-width="1.4" fill="none"/></svg></span>
      </div>
    </div>
  </div>

  <div class="abs card" style="left:63px"><div class="photo" role="img" aria-label="White kitchen with island and pendant lights" style="background:linear-gradient(160deg,#8a7a68,#e0dcd4 60%,#6b5a48)"></div><h3>CREATE BATHROOM</h3><p>Lorem ipsum dolor sit amet, consectetur adipiscing elit, sed do eiusmod tempor incididunt</p></div>
  <div class="abs card" style="left:227px"><div class="photo" role="img" aria-label="Kitchen with cream cabinets and range hood" style="background:linear-gradient(160deg,#5a4a3c,#d8d0c2 55%,#3a2e26)"></div><h3>LIVING ROOM</h3><p>Lorem ipsum dolor sit amet, consectetur adipiscing elit, sed do eiusmod tempor incididunt</p></div>
  <div class="abs card" style="left:391px"><div class="photo" role="img" aria-label="Dark wood cabinet island" style="background:linear-gradient(160deg,#d8d2c6,#2a2320 50%,#5a4030)"></div><h3>BEDROOM CABINETS</h3><p>Lorem ipsum dolor sit amet, consectetur adipiscing elit, sed do eiusmod tempor incididunt</p></div>
  <div class="abs card" style="left:554px"><div class="photo" role="img" aria-label="White entertainment unit with television" style="background:linear-gradient(180deg,#3a3a3a,#e8e6e2 55%,#5a3a26)"></div><h3>ENTERTAINMENT</h3><p>Lorem ipsum dolor sit amet, consectetur adipiscing elit, sed do eiusmod tempor incididunt</p></div>

  <section class="abs welcome">
    <h1>Welcome To Bramblewood Joinery</h1>
    <p>Lorem ipsum dolor sit amet, consectetur adipiscing elit, sed do eiusmod tempor incididunt ut labore et dolore magna aliqua. Ut enim ad minim veniam, quis nostrud exercitation ullamco laboris nisi ut aliquip ex ea commodo consequat. Duis aute irure dolor in reprehenderit in voluptate velit esse cillum fugiat nulla pariatur. Lorem ipsum dolor sit amet, consectetur adipiscing elit.</p>
  </section>
  <ul class="abs ticks welcome-list">
    <li><span class="tick"><svg width="5" height="5" viewBox="0 0 6 6"><path d="M2 1l2 2-2 2" stroke="#fff" fill="none"/></svg></span>Kitchen Cabinets</li>
    <li><span class="tick"><svg width="5" height="5" viewBox="0 0 6 6"><path d="M2 1l2 2-2 2" stroke="#fff" fill="none"/></svg></span>Entertainment Centers</li>
    <li><span class="tick"><svg width="5" height="5" viewBox="0 0 6 6"><path d="M2 1l2 2-2 2" stroke="#fff" fill="none"/></svg></span>Kitchen Islands</li>
    <li><span class="tick"><svg width="5" height="5" viewBox="0 0 6 6"><path d="M2 1l2 2-2 2" stroke="#fff" fill="none"/></svg></span>TV Cabinets</li>
    <li><span class="tick"><svg width="5" height="5" viewBox="0 0 6 6"><path d="M2 1l2 2-2 2" stroke="#fff" fill="none"/></svg></span>Bathroom Cabinets</li>
    <li><span class="tick"><svg width="5" height="5" viewBox="0 0 6 6"><path d="M2 1l2 2-2 2" stroke="#fff" fill="none"/></svg></span>Commercial &amp; Wood hood</li>
  </ul>
  <div class="abs btn">WATCH MORE VIDEOS</div>

  <div class="abs video">
    <div class="frame" role="img" aria-label="Video still of a dark wood kitchen island">
      <svg width="259" height="164"><circle cx="133" cy="96" r="23" fill="rgba(255,255,255,.35)"/><path d="M125 84v24l20-12z" fill="rgba(60,60,60,.8)"/></svg>
    </div>
    <div class="bar">
      <svg width="5" height="6"><path d="M0 0v6l5-3z" fill="#333"/></svg>
      <span>10:00/05:03</span>
      <span style="flex:1;height:2px;background:linear-gradient(90deg,#e03a2a 45%,#555 45%);margin-left:14px"></span>
      <svg width="8" height="6"><path d="M0 2h2l3-2v6l-3-2H0z" fill="#333"/></svg>
      <span style="width:24px;height:2px;background:#e03a2a"></span>
    </div>
  </div>

  <section class="abs banner">
    <h2>Kansas City’s Premier Custom Kitchen<br>Cabinet Design Company</h2>
    <ul class="ticks">
      <li><span class="tick"><svg width="5" height="5" viewBox="0 0 6 6"><path d="M2 1l2 2-2 2" stroke="#fff" fill="none"/></svg></span>Cabinet Hardware</li>
      <li><span class="tick"><svg width="5" height="5" viewBox="0 0 6 6"><path d="M2 1l2 2-2 2" stroke="#fff" fill="none"/></svg></span>Customer Experience</li>
      <li><span class="tick"><svg width="5" height="5" viewBox="0 0 6 6"><path d="M2 1l2 2-2 2" stroke="#fff" fill="none"/></svg></span>Commercial &amp; Wood hood</li>
      <li><span class="tick"><svg width="5" height="5" viewBox="0 0 6 6"><path d="M2 1l2 2-2 2" stroke="#fff" fill="none"/></svg></span>Door &amp; Drawer Styles</li>
    </ul>
    <div class="abs truck" role="img" aria-label="Green delivery truck with kitchen photo on its box"></div>
  </section>

  <div class="abs foot-band"></div>
  <div class="abs foot-item" style="left:63px;top:1101px">
    <div class="round-icon"><svg width="14" height="12" viewBox="0 0 14 12"><path d="M7 0L0 6h2v6h4V8h2v4h4V6h2z" fill="#888"/></svg></div>
    <div>Bramblewood Joinery Owen Hartley<br>4820 Alder Lane Fernhill, MO 64000</div>
  </div>
  <div class="abs foot-item" style="left:340px;top:1101px">
    <div class="round-icon"><svg width="12" height="12" viewBox="0 0 24 24"><path fill="#888" d="M6.6 10.8a15 15 0 006.6 6.6l2.2-2.2c.3-.3.7-.4 1-.2 1.1.4 2.3.6 3.6.6.6 0 1 .4 1 1V20c0 .6-.4 1-1 1A17 17 0 013 4c0-.6.4-1 1-1h3.5c.6 0 1 .4 1 1 0 1.3.2 2.5.6 3.6.1.3 0 .7-.2 1z"/></svg></div>
    <div>Phone No : +1 555.014.2300<br>Email: info@bramblewoodjoinery.example</div>
  </div>
  <div class="abs social" aria-label="Social links">
    <span><svg width="10" height="10" viewBox="0 0 10 10"><circle cx="7.5" cy="2" r="1.5" fill="#fff"/><circle cx="2.5" cy="5" r="1.5" fill="#fff"/><circle cx="7.5" cy="8" r="1.5" fill="#fff"/><path d="M7.5 2L2.5 5l5 3" stroke="#fff" fill="none"/></svg></span>
    <span><svg width="10" height="8" viewBox="0 0 10 8"><rect x=".5" y=".5" width="9" height="7" fill="none" stroke="#fff"/><path d="M.5 .5l4.5 4 4.5-4" stroke="#fff" fill="none"/></svg></span>
    <span><svg width="10" height="10" viewBox="0 0 10 10"><circle cx="5" cy="5" r="4.3" fill="none" stroke="#fff"/><path d="M.7 5h8.6M5 .7c-2.4 2.4-2.4 6.2 0 8.6M5 .7c2.4 2.4 2.4 6.2 0 8.6" stroke="#fff" fill="none" stroke-width=".8"/></svg></span>
    <span><svg width="10" height="9" viewBox="0 0 10 9"><path d="M1 1h8v5H4l-2 2V6H1z" fill="#fff"/></svg></span>
  </div>

  <footer class="abs bottom">
    <span>© 2015 Bramblewood Joinery. All rights reserved.</span>
    <nav><span>Home</span>/<span>About Us</span>/<span>Photo Gallery</span>/<span>Contact Us</span></nav>
  </footer>
</div>
</body>
</html>
```